Landscape design build company door flyer

I would like this flyer to convey a high-level of professionalism for a company that is excellent with communication with their clients as well as a company that does incredible installations

Went on vacation/holiday

```html
<!DOCTYPE html>
<html lang="en">
<head>
<meta charset="utf-8">
<title>Cedarline Builders – Outdoor Living Flyer</title>
<link rel="stylesheet" href="https://fonts.googleapis.com/css2?family=Poppins:wght@400;500;600;700;800&display=swap">
<style>
  :root{
    --navy:#0b2b40;
    --gold:#fbb200;
    --paper:#f1f1f1;
    --ink:#1b1b1b;
    --stage:#808080;
    --photo-green:#55704a;
    --photo-slate:#5d6a72;
  }
  *{margin:0;padding:0;box-sizing:border-box}
  html,body{width:1200px;height:933px;overflow:hidden}
  body{background:var(--stage);font-family:'Poppins',sans-serif;position:relative}
  .flyer{position:absolute;left:258px;top:26px;width:684px;height:880px;background:var(--paper);overflow:hidden;box-shadow:0 8px 30px rgba(0,0,0,.35)}
  .hero{position:absolute;left:0;top:0;width:684px;height:414px}
  .brand{position:absolute;left:0;top:72px;width:270px;text-align:center;color:var(--navy)}
  .brand-name{font-weight:600;font-size:16px;letter-spacing:.3px;line-height:1.1}
  .brand-tag{font-weight:500;font-size:7px;letter-spacing:.2px;margin-top:2px}
  .headline{position:absolute;left:31px;top:176px;font-weight:700;font-size:48px;line-height:50px;letter-spacing:-.3px;color:#fff;text-transform:uppercase}
  .headline .accent{color:var(--gold)}
  .section-title{font-weight:800;font-size:21px;color:var(--navy);line-height:1;text-transform:uppercase;letter-spacing:-.2px}
  .section-rule{width:59px;height:3px;background:var(--gold);margin:9px 0 8px}
  .about{position:absolute;left:30px;top:440px;width:290px}
  .about p{font-size:10.4px;line-height:13.1px;color:var(--ink);text-align:justify;letter-spacing:.25px}
  .services{position:absolute;left:376px;top:440px}
  .services ul{list-style:none;margin-top:10px}
  .services li{display:flex;align-items:center;gap:12px;height:18.6px;font-size:11.6px;font-weight:500;color:var(--navy)}
  .services svg{width:11px;height:11px;flex:none}
  .works-rule{position:absolute;left:0;top:631px;width:684px;height:1px;background:var(--gold)}
  .works-label{position:absolute;left:242px;top:618px;width:193px;height:26px;background:var(--gold);color:#fff;font-weight:800;font-size:16px;text-align:center;line-height:27px;text-transform:uppercase}
  .works{position:absolute;top:655px;left:35px;display:flex;gap:26px}
  .work{width:185px;height:101px}
  .work.deck{background:linear-gradient(160deg,#4f7a3c 0%,#8a5a3a 55%,#6d3b24 100%)}
  .work.pool{background:linear-gradient(135deg,#3d5a36 0%,#b9c2c6 40%,#5fc6c0 55%,#d0d5d8 100%)}
  .work.firepit{background:linear-gradient(160deg,#2f3a33 0%,#6a6462 50%,#8a6a4c 100%)}
  .footer{position:absolute;left:0;top:792px;width:684px;height:88px}
  .phone{position:absolute;left:42px;top:814px;display:flex;align-items:center;gap:10px;color:var(--gold);font-weight:700;font-size:40px;line-height:1;letter-spacing:-.5px}
  .phone svg{width:26px;height:28px}
  .contact{position:absolute;left:447px;top:810px;color:#fff;font-size:12.6px;font-weight:500}
  .contact div{display:flex;align-items:center;gap:17px;height:22.5px}
  .contact svg{width:15px;height:12px;flex:none}
</style>
</head>
<body>
<main class="flyer">
  <svg class="hero" viewBox="0 0 684 414" aria-hidden="false">
    <defs>
      <linearGradient id="heroPhoto" x1="0" y1="0" x2="1" y2="1">
        <stop offset="0" stop-color="#4d6b3e"/>
        <stop offset=".45" stop-color="#6c7880"/>
        <stop offset="1" stop-color="#4a4e50"/>
      </linearGradient>
    </defs>
    <rect width="684" height="140" fill="#f1f1f1"/>
    <g role="img" aria-label="Aerial photo of a house with a paver driveway, steps and planted beds">
      <polygon points="315,0 684,0 684,414 457,414 321,140 267,140" fill="url(#heroPhoto)"/>
    </g>
    <polygon points="0,140 321,140 457,414 0,414" fill="#0b2b40"/>
  </svg>

  <div class="brand">
    <div class="brand-name">CEDARLINE BUILDERS</div>
    <div class="brand-tag">OUTDOOR LIVING SPACES</div>
  </div>

  <h1 class="headline">Let’s create<br>your dream<br><span class="accent">outdoor<br>living space!</span></h1>

  <section class="about">
    <h2 class="section-title">About us</h2>
    <div class="section-rule"></div>
    <p>Discover the endless possibilities for your outdoor space with The Cedarline Builders Team. Our team of skilled artisans is dedicated to turning your outdoor space into a breathtaking oasis that you’ll love coming home to. Whether it’s a cozy patio for intimate gatherings, a sprawling deck to host memorable parties, or a custom paver driveway that adds instant curb appeal, our high-quality craftsmanship ensures stunning results that exceed your expectations.</p>
  </section>

  <section class="services">
    <h2 class="section-title">Our services</h2>
    <div class="section-rule"></div>
    <ul>
      <li><svg viewBox="0 0 12 12"><circle cx="6" cy="6" r="6" fill="#0b2b40"/><path d="M3.2 6.2l1.9 1.9 3.7-3.9" stroke="#fff" stroke-width="1.5" fill="none"/></svg>Paver Patios</li>
      <li><svg viewBox="0 0 12 12"><circle cx="6" cy="6" r="6" fill="#0b2b40"/><path d="M3.2 6.2l1.9 1.9 3.7-3.9" stroke="#fff" stroke-width="1.5" fill="none"/></svg>Paver Driveways</li>
      <li><svg viewBox="0 0 12 12"><circle cx="6" cy="6" r="6" fill="#0b2b40"/><path d="M3.2 6.2l1.9 1.9 3.7-3.9" stroke="#fff" stroke-width="1.5" fill="none"/></svg>Retaining Walls</li>
      <li><svg viewBox="0 0 12 12"><circle cx="6" cy="6" r="6" fill="#0b2b40"/><path d="M3.2 6.2l1.9 1.9 3.7-3.9" stroke="#fff" stroke-width="1.5" fill="none"/></svg>Decks &amp; Railings</li>
      <li><svg viewBox="0 0 12 12"><circle cx="6" cy="6" r="6" fill="#0b2b40"/><path d="M3.2 6.2l1.9 1.9 3.7-3.9" stroke="#fff" stroke-width="1.5" fill="none"/></svg>Pools</li>
      <li><svg viewBox="0 0 12 12"><circle cx="6" cy="6" r="6" fill="#0b2b40"/><path d="M3.2 6.2l1.9 1.9 3.7-3.9" stroke="#fff" stroke-width="1.5" fill="none"/></svg>Outdoor Lighting</li>
      <li><svg viewBox="0 0 12 12"><circle cx="6" cy="6" r="6" fill="#0b2b40"/><path d="M3.2 6.2l1.9 1.9 3.7-3.9" stroke="#fff" stroke-width="1.5" fill="none"/></svg>Firepits &amp; Fireplaces</li>
    </ul>
  </section>

  <div class="works-rule"></div>
  <div class="works-label">Our works</div>
  <div class="works">
    <div class="work deck" role="img" aria-label="Photo of a wooden deck with pergola and patio chairs"></div>
    <div class="work pool" role="img" aria-label="Aerial photo of a plunge pool with grey composite decking"></div>
    <div class="work firepit" role="img" aria-label="Photo of a lit paver patio with a sunken fire pit and pool"></div>
  </div>

  <svg class="footer" viewBox="0 0 684 88" aria-hidden="true">
    <rect x="0" y="6" width="684" height="82" fill="#0b2b40"/>
    <polygon points="417,0 684,0 684,88 379,88" fill="#fbb200"/>
  </svg>
  <div class="phone">
    <svg viewBox="0 0 24 26"><path d="M6 1.5l3.4 5.2-2.4 2.3c1.3 3.5 3.8 6.3 7.2 8.1l2.4-2.3 5.3 3.4-1.6 4.4c-.4 1-1.5 1.6-2.6 1.3C9.2 21.8 2.7 14.6 1.2 6.4 1 5.3 1.6 4.2 2.6 3.8z" fill="#fbb200"/></svg>
    <span>206-555-0148</span>
  </div>
  <div class="contact">
    <div><svg viewBox="0 0 15 12"><rect width="15" height="12" rx="1" fill="#fff"/><path d="M1 1.5l6.5 5 6.5-5" stroke="#fbb200" stroke-width="1.4" fill="none"/></svg>info@cedarlinebuilders.com</div>
    <div><svg viewBox="0 0 14 14"><g fill="none" stroke="#fff" stroke-width="1.1"><circle cx="7" cy="7" r="6"/><ellipse cx="7" cy="7" rx="2.6" ry="6"/><path d="M1 7h12M2 4h10M2 10h10"/></g></svg>www.cedarlinebuilders.com</div>
  </div>
</main>
</body>
</html>
```